Bref créative
Business card and stationery for painting company
Brightwall finishes
Professional
Tomas Renko
Owner
318 S Harlow Rd suite 207
Marden Hills, IL 60294
tomas.renko@brightwallfinishes.example
www.brightwallfinishes.example
this is file of my logo
vector logo file

```html
<!DOCTYPE html>
<html lang="en">
<head>
<meta charset="utf-8">
<title>Brightwall finishes — Stationery</title>
<link rel="stylesheet" href="https://fonts.googleapis.com/css2?family=Open+Sans:wght@400;700&display=swap">
<style>
:root{
  --backdrop:#e9e4dc;
  --paper:#ffffff;
  --paper-edge:#dcd7cf;
  --brand-red:#d6232b;
  --brand-blue:#2c4fa6;
  --ink:#444a55;
  --label:#6d6760;
  --faint:#ecd9d9;
}
*{margin:0;padding:0;box-sizing:border-box}
html,body{width:1200px;height:446px;overflow:hidden}
body{background:var(--backdrop);font-family:"Open Sans",Arial,sans-serif;color:var(--ink);position:relative}
.sheet{position:absolute;background:var(--paper);box-shadow:0 2px 6px rgba(0,0,0,.18)}
.label{position:absolute;font-size:6px;letter-spacing:.5px;text-transform:uppercase;color:var(--label);white-space:nowrap}
.brand{display:flex;align-items:center;gap:4px;font-weight:700;color:var(--brand-blue);text-transform:uppercase;white-space:nowrap}
.brand .dot{width:8px;height:8px;border-radius:50%;background:var(--brand-red);flex:none}
.section-title{left:18px;top:120px}
.card{left:19px;width:125px;height:62px}
.card-front{top:156px;display:flex;flex-direction:column;justify-content:space-between;padding:7px}
.card-front .brand{font-size:7px}
.card-front .band{height:14px;background:var(--brand-red);margin:0 -7px -7px;display:flex;align-items:center;padding-left:7px;font-size:5px;color:#fff}
.card-back{top:232px;display:flex;align-items:center;justify-content:center}
.card-back .brand{font-size:8px}
.letterhead{top:12px;width:236px;height:414px;padding:14px 16px}
.letterhead-one{left:164px}
.letterhead-two{left:474px}
.letterhead .head{display:flex;justify-content:space-between;align-items:flex-start}
.letterhead .brand{font-size:9px}
.contact{font-size:4px;line-height:6.5px;color:var(--ink);list-style:none}
.contact li::before{content:"";display:inline-block;width:3px;height:3px;background:var(--brand-red);margin-right:3px;vertical-align:middle}
.mark-faint{position:absolute;left:0;right:0;top:150px;display:flex;justify-content:center}
.mark-faint .brand{font-size:14px;color:var(--faint)}
.mark-faint .brand .dot{width:18px;height:18px;background:var(--faint)}
.letterhead .foot{position:absolute;left:0;right:0;bottom:14px;font-size:4px;text-align:center}
.envelope-back{left:846px;top:0;width:290px;height:300px}
.envelope-front{left:836px;top:318px;width:270px;height:116px;padding:12px 14px}
.envelope-front .brand{font-size:9px}
.envelope-front .address{font-size:4px;line-height:6px;margin-top:4px}
.envelope-front .mark-faint{top:62px}
.envelope-front .mark-faint .brand{font-size:10px}
.envelope-front .mark-faint .brand .dot{width:12px;height:12px}
</style>
</head>
<body>
<span class="label section-title">Stationery Concepts</span>

<section class="sheet card card-front">
  <div class="brand"><span class="dot"></span>Brightwall finishes</div>
  <div class="band">Tomas Renko · Owner</div>
</section>
<span class="label" style="left:19px;top:221px">Business Card Front</span>

<section class="sheet card card-back">
  <div class="brand"><span class="dot"></span>Brightwall finishes</div>
</section>
<span class="label" style="left:19px;top:297px">Business Card Back</span>

<section class="sheet letterhead letterhead-one">
  <div class="head">
    <div class="brand"><span class="dot"></span>Brightwall finishes</div>
    <ul class="contact">
      <li>318 S Harlow Rd suite 207</li>
      <li>Marden Hills, IL 60294</li>
      <li>tomas.renko@brightwallfinishes.example</li>
      <li>www.brightwallfinishes.example</li>
    </ul>
  </div>
  <div class="mark-faint"><div class="brand"><span class="dot"></span>Brightwall finishes</div></div>
</section>
<span class="label" style="left:250px;top:430px">Letterhead Option 1</span>

<section class="sheet letterhead letterhead-two">
  <div class="head" style="justify-content:center">
    <div class="brand"><span class="dot"></span>Brightwall finishes</div>
  </div>
  <div class="mark-faint"><div class="brand"><span class="dot"></span>Brightwall finishes</div></div>
  <div class="foot">318 S Harlow Rd suite 207, Marden Hills, IL 60294 · tomas.renko@brightwallfinishes.example · www.brightwallfinishes.example</div>
</section>
<span class="label" style="left:560px;top:430px">Letterhead Option 2</span>

<svg class="envelope-back" style="position:absolute" viewBox="0 0 290 300" aria-hidden="true">
  <rect x="0" y="0" width="290" height="132" fill="var(--brand-red)"/>
  <path d="M0 0 H290 V40 Q145 70 0 40 Z" fill="#e04a50"/>
  <rect x="6" y="92" width="278" height="150" fill="var(--brand-blue)"/>
  <path d="M6 92 H284 L150 172 Q145 175 140 172 Z" fill="#3d62bd"/>
  <rect x="6" y="222" width="278" height="70" fill="var(--paper)" stroke="var(--paper-edge)"/>
  <path d="M6 222 L145 262 L284 222" fill="none" stroke="var(--paper-edge)"/>
</svg>

<section class="sheet envelope-front">
  <div class="brand"><span class="dot"></span>Brightwall finishes</div>
  <div class="address">318 S Harlow Rd suite 207<br>Marden Hills, IL 60294</div>
  <div class="mark-faint"><div class="brand"><span class="dot"></span>Brightwall finishes</div></div>
</section>
<span class="label" style="left:1112px;top:430px">Envelope Option 1</span>
</body>
</html>
```